Delia Marsh Catalog to submit to vendors

We need a catalog made with all of the products in our shop for sales purposes. Our Website is www.deliamarshandcompany.example
Almost all of our products are listed on the website. If you can not take the pictures from the site I can upload them. The descriptions are listed as well. There are three additional products that I will upload. This Catalog will be mailed to stores and should include MSRP Prices.
Updates

Hello There-We are looking for a sales catalog to send to stores in our area. We would like to include MSRP and the end we can add wholesale pricing with minimum orders. Our website is www.deliamarshandcompany.example. There are a few products that haven't been added to the website yet. Where can I upload them and send descriptions?Thank you,Colette Added Thursday, January 21, 2016

Target Market(s)

boutiques and gift shops

Industry/Entity Type

Shop

Font styles to use
Serif
Other font styles liked:
• Noteworthy

Colors
e34297
a64599
6b449b
0255a3

Requirements
Must have
• Color! I would like to organize the catalog by sections. Our premade section and our DIY kits. Maybe we should include Gift sets and put the baskets and gift boxes in one section

```html
<!DOCTYPE html>
<html lang="en">
<head>
<meta charset="utf-8">
<title>Delia Marsh Catalog – DIY Kits and Gift Sets</title>
<link rel="stylesheet" href="https://fonts.googleapis.com/css2?family=Itim&family=Fresca&display=swap">
<style>
  :root {
    --blue: #0255a3;
    --pink: #e34297;
    --violet: #a64599;
    --purple: #6b449b;
    --label-pink: #e0559f;
    --paper: #ffffff;
    --backdrop: #ecebf0;
  }
  * { margin: 0; padding: 0; box-sizing: border-box; }
  html, body { width: 1200px; height: 1000px; overflow: hidden; }
  body { background: var(--backdrop); position: relative; font-family: "Fresca", sans-serif; }

  .catalog-strip {
    position: absolute; left: 10px; top: 281px; width: 1176px; height: 416px;
    background: var(--paper);
    box-shadow: 0 2px 6px rgba(60, 50, 80, .25);
  }
  .section { position: absolute; top: 0; width: 588px; height: 416px; }
  .section--diy { left: 0; }
  .section--gifts { left: 588px; }
  .section__band { position: absolute; left: 0; bottom: 0; width: 100%; height: 23px; }
  .section--diy .section__band { background: var(--blue); }
  .section--gifts .section__band { background: var(--pink); }

  .section__title { position: absolute; top: 15px; left: 30px; width: 548px; height: 58px; }
  .section__title svg { position: absolute; inset: 0; }
  .section__title h2 {
    position: relative; height: 48px; line-height: 50px; text-align: center;
    padding-right: 32px;
    font-family: "Itim", sans-serif; font-weight: 400; font-size: 34px; color: #fff;
  }

  .product { position: absolute; width: 190px; text-align: center; }
  .product__photo {
    width: 180px; height: 180px; margin: 0 auto; border-radius: 50%; border: 8px solid;
  }
  .section--diy .product__photo { border-color: var(--blue); }
  .section--gifts .product__photo { border-color: var(--pink); }
  .product__name { margin-top: 10px; font-size: 17px; line-height: 18px; color: var(--label-pink); font-weight: 400; }
  .product__name--airy { line-height: 21px; margin-top: 8px; }
  .product__price { margin-top: 8px; font-size: 21px; color: var(--purple); }

  .photo--lipbalm { background: linear-gradient(160deg, #f4eef4 0%, #e6a9d0 55%, #c95aa8 100%); }
  .photo--meteor { background: linear-gradient(170deg, #3d4fc0 0%, #5967d4 45%, #e9ebf2 100%); }
  .photo--party { background: linear-gradient(160deg, #d23c98 0%, #c97ab6 50%, #f1e6ee 100%); }
  .photo--cupcake { background: linear-gradient(180deg, #f7f7f7 0%, #ea7cb6 55%, #7fc7c9 100%); }
  .photo--flowers { background: linear-gradient(160deg, #f0e58f 0%, #f0b7c9 45%, #9fcbea 100%); }
  .photo--hearts { background: linear-gradient(160deg, #c69ad8 0%, #9fd8cf 50%, #a9b3ea 100%); }
</style>
</head>
<body>
  <main class="catalog-strip">
    <section class="section section--diy">
      <div class="section__title">
        <svg width="548" height="58" viewBox="0 0 548 58" aria-hidden="true">
          <path d="M24 0 H524 A24 24 0 0 1 524 48 H510 L542 57 L522 48 H24 A24 24 0 0 1 24 0 Z" fill="var(--blue)"/>
        </svg>
        <h2>Do It Yourself Kit</h2>
      </div>
      <article class="product" style="left:10px; top:102px;">
        <div class="product__photo photo--lipbalm" role="img" aria-label="Photo of the lip balm kit: box, jars and balm base on a pink table"></div>
        <h3 class="product__name">Lip Balm Kit</h3>
        <p class="product__price">from $28.00</p>
      </article>
      <article class="product" style="left:200px; top:127px;">
        <div class="product__photo photo--meteor" role="img" aria-label="Photo of the meteor bath fizz kit: bowl of powder, bottles and bath bombs on blue"></div>
        <h3 class="product__name" style="margin-top:8px;">Meteor Bath<br>Fizz Kit</h3>
        <p class="product__price" style="margin-top:0;">$16.00</p>
      </article>
      <article class="product" style="left:388px; top:102px;">
        <div class="product__photo photo--party" role="img" aria-label="Photo of the party kit: jars, bottles and supplies on a pink table"></div>
        <h3 class="product__name">Party Kit</h3>
        <p class="product__price" style="margin-top:12px;">$99.00</p>
      </article>
      <div class="section__band"></div>
    </section>

    <section class="section section--gifts">
      <div class="section__title">
        <svg width="548" height="58" viewBox="0 0 548 58" aria-hidden="true">
          <path d="M24 0 H524 A24 24 0 0 1 524 48 H510 L542 57 L522 48 H24 A24 24 0 0 1 24 0 Z" fill="var(--pink)"/>
        </svg>
        <h2>Gift Sets And Boxes</h2>
      </div>
      <article class="product" style="left:7px; top:102px;">
        <div class="product__photo photo--cupcake" role="img" aria-label="Photo of soap and bath bomb cupcakes in purple, pink and teal"></div>
        <h3 class="product__name">Soap &amp; Bath Bomb<br>Cupcake Combo<br>(Multi-Color)</h3>
        <p class="product__price" style="margin-top:6px;">$from 6.00</p>
      </article>
      <article class="product" style="left:197px; top:127px;">
        <div class="product__photo photo--flowers" role="img" aria-label="Photo of pastel flower-shaped bath bombs in a gift box"></div>
        <h3 class="product__name product__name--airy" style="margin-top:4px;">Bath Bomb<br>Flowers Gift Pack</h3>
        <p class="product__price" style="margin-top:9px;">$18.00</p>
      </article>
      <article class="product" style="left:387px; top:102px;">
        <div class="product__photo photo--hearts" role="img" aria-label="Photo of pastel heart-shaped bath bombs in a gift box"></div>
        <h3 class="product__name product__name--airy">Bath Bomb Hearts<br>Gift Pack</h3>
        <p class="product__price" style="margin-top:14px;">$18.00</p>
      </article>
      <div class="section__band"></div>
    </section>
  </main>
</body>
</html>
```